Stationery Set for Velmora Company

I need to create full stationery design for my company; Business Cards, Envelops, Letter Heads, Calendar.
In the letter head and Envelops... only contact information and website links.
Our company is a Service Management company with different domains of innovative services including Technology Service Management, Education Services, Outsourcing Management, Events Management.
I need a modern and innovative design specially for the business card. I some transparent designs and I like it, but don't limit your innovation to what I mentioned. Sky is limit for your innovation.

Target Market(s)

Middle East & Africa

Industry/Entity Type

Business Management

Colors
34a7d8
0355a3
85acd3
86cae7
cee9f5
cfdeed
e4daeb
f3f1f8
ecf7fb

Requirements
Must have
• Name, Title, Email, Mobile
Nice to have
• We have multiple locations in USA, KSA, EGY, so I need ideas about how to include all contact details maybe QR / Barcode or something else.
• Please see our locations and contact information: www.brightvelmora.example
Should not have
• Too much text

```html
<!DOCTYPE html>
<html lang="en">
<head>
<meta charset="utf-8">
<title>Velmora Company – Business Card</title>
<link href="https://fonts.googleapis.com/css2?family=Arimo:wght@400;700&display=swap" rel="stylesheet">
<style>
  :root{
    --stage:#e9eaec;
    --card:#ffffff;
    --brand-blue:#3f72c0;
    --ink:#1f1f1f;
    --muted:#555a60;
    --rule:#c9ccd1;
  }
  *{box-sizing:border-box;margin:0;padding:0}
  html,body{width:1200px;height:750px;overflow:hidden}
  body{
    background:var(--stage);
    font-family:"Arimo",Arial,sans-serif;
    color:var(--ink);
    position:relative;
  }
  .card{
    position:absolute;
    width:525px;height:300px;
    background:var(--card);
    box-shadow:0 10px 26px rgba(0,0,0,.18);
    overflow:hidden;
  }
  .card--front{left:50px;top:225px}
  .card--back{left:625px;top:225px}

  .brand{display:flex;align-items:center;gap:10px}
  .brand__mark{width:16px;height:16px;background:var(--brand-blue)}
  .brand__name{font-weight:700;color:var(--brand-blue);font-size:26px;letter-spacing:.5px}

  .card--front .brand{position:absolute;left:0;right:0;top:108px;justify-content:center}
  .front__web{
    position:absolute;left:0;right:0;top:190px;text-align:center;
    font-size:12px;letter-spacing:2px;color:var(--ink);
  }

  .card--back .brand{position:absolute;right:34px;top:28px}
  .card--back .brand__name{font-size:22px}

  .contact{
    position:absolute;right:28px;top:84px;list-style:none;
    font-size:12px;line-height:18px;text-align:right;
  }
  .contact li{display:flex;justify-content:flex-end;align-items:center;gap:8px}
  .contact svg{width:11px;height:11px;fill:var(--brand-blue)}

  .holder{position:absolute;left:0;top:168px}
  .holder__tab{position:absolute;left:0;top:4px;width:6px;height:30px;background:var(--brand-blue)}
  .holder__name{position:absolute;left:44px;top:0;font-size:17px;color:var(--brand-blue);white-space:nowrap}
  .holder__title{position:absolute;left:56px;top:21px;font-size:13px;white-space:nowrap}

  .office{position:absolute;left:70px;font-size:12px;line-height:15px}
  .office--usa{top:214px}
  .office--ksa{top:268px;left:240px;top:180px}
  .office__label{color:var(--brand-blue);font-size:12px;text-transform:uppercase}

  .base-rule{position:absolute;left:0;right:0;bottom:7px;height:2px;background:var(--rule)}
  .base-band{position:absolute;left:0;right:0;bottom:0;height:6px;background:var(--brand-blue)}
</style>
</head>
<body>

<section class="card card--front" aria-label="Business card front">
  <div class="brand">
    <span class="brand__mark"></span>
    <span class="brand__name">Velmora Company</span>
  </div>
  <p class="front__web">www.brightvelmora.example</p>
</section>

<section class="card card--back" aria-label="Business card back">
  <div class="brand">
    <span class="brand__mark"></span>
    <span class="brand__name">Velmora Company</span>
  </div>

  <ul class="contact">
    <li>+1.555 010 4570 (USA)
      <svg viewBox="0 0 12 12"><path d="M2 1h3l1 3-2 1a7 7 0 0 0 3 3l1-2 3 1v3c-6 0-10-4-10-9z"/></svg></li>
    <li>+966 555 010 425 (Saudi Arabia)
      <svg viewBox="0 0 12 12"><path d="M2 1h3l1 3-2 1a7 7 0 0 0 3 3l1-2 3 1v3c-6 0-10-4-10-9z"/></svg></li>
    <li>+1.555 010 4570
      <svg viewBox="0 0 12 12"><path d="M3 0h6v12H3zM4 1v9h4V1z"/></svg></li>
    <li>info@brightvelmora.example
      <svg viewBox="0 0 12 12"><path d="M0 2h12v8H0zM1 3l5 4 5-4z"/></svg></li>
    <li>www.brightvelmora.example
      <svg viewBox="0 0 12 12"><circle cx="6" cy="6" r="5.5"/></svg></li>
  </ul>

  <div class="holder">
    <span class="holder__tab"></span>
    <span class="holder__name">Aria Lenholt</span>
    <span class="holder__title">President</span>
  </div>

  <div class="office office--usa" style="left:40px;top:218px">
    <p class="office__label">USA</p>
    <p>48 Harbor Crest Lane</p>
    <p>4th Floor Maple Bay</p>
    <p>CA 90000 US</p>
  </div>

  <div class="office office--ksa" style="left:200px;top:196px">
    <p class="office__label">Saudi Arabia</p>
    <p>Riyadh, Al Noor District,</p>
    <p>Qasr Tower St.</p>
    <p>Sarwa Buildings</p>
    <p>Block 4C 3rd Floor C12, C14</p>
  </div>

  <div class="base-rule"></div>
  <div class="base-band"></div>
</section>

</body>
</html>
```